Computer Training in the Education sector - Letterhead

We need a new letter head to be designed for the company. We provide computer training fro the Education Sector, both primary and private tertiary providers. The colours will need to tie in with the website www.crossingthestream.co.nz.
The company name is Crossing the Stream with the tag line of Computer Training for Educators.
The footer will need to have the following detail...
0508 PCS MENTOR
021 839 415
www.crossingthestream.co.nz / training@crossingthestream.co.nz
Updates

Thanks for the designs so far.

Some have watermarks in the background. Please don't worry about using watermarks as I will not be using a watermark in in a final design.
Regards,
Roger

Thank you for all the designs and the effort. There was some great concepts that came through.

Cheers
Roger

Industry/Entity Type

Computer

```html
<!DOCTYPE html>
<html lang="en">
<head>
<meta charset="utf-8">
<title>Crossing the Stream – Letterhead</title>
<link rel="stylesheet" href="https://fonts.googleapis.com/css2?family=Arimo:wght@400;700&display=swap">
<style>
  :root {
    --paper: #ffffff;
    --ink: #2b2b2b;
    --brand-blue: #2e74b8;
    --brand-green: #8cbb3f;
    --brand-orange: #e5832f;
    --rule: #555555;
  }
  * { margin: 0; padding: 0; box-sizing: border-box; }
  html, body {
    width: 1034px;
    height: 1200px;
    overflow: hidden;
    background: var(--paper);
  }
  .letterhead {
    position: relative;
    width: 1034px;
    height: 1200px;
    background: var(--paper);
    font-family: "Arimo", Arial, sans-serif;
    color: var(--ink);
  }
  .brand {
    position: absolute;
    left: 57px;
    top: 58px;
    display: flex;
    align-items: center;
    gap: 12px;
  }
  .brand-dot {
    width: 18px;
    height: 18px;
    border-radius: 50%;
    background: var(--brand-blue);
  }
  .brand-name {
    font-size: 26px;
    font-weight: 700;
    color: var(--brand-blue);
    line-height: 1.2;
  }
  .contact {
    position: absolute;
    left: 658px;
    top: 45px;
    height: 84px;
    border-left: 1px solid var(--rule);
    padding-left: 20px;
    display: flex;
    flex-direction: column;
    justify-content: space-between;
    padding-top: 4px;
    padding-bottom: 4px;
    list-style: none;
  }
  .contact-item {
    display: flex;
    align-items: center;
    gap: 6px;
    font-size: 17px;
    letter-spacing: 0.3px;
    line-height: 1;
  }
  .contact-icon { width: 14px; height: 14px; flex: none; }
  .tagline {
    position: absolute;
    left: 33px;
    top: 1150px;
    font-size: 18px;
    font-weight: 700;
    letter-spacing: 1.4px;
    color: var(--brand-orange);
  }
  .footer-bands {
    position: absolute;
    left: 0;
    bottom: 0;
    width: 1034px;
    height: 46px;
  }
  .web-address {
    position: absolute;
    left: 570px;
    top: 1166px;
    font-size: 17px;
    letter-spacing: 1.3px;
    color: var(--paper);
  }
</style>
</head>
<body>
<div class="letterhead">
  <header>
    <div class="brand">
      <span class="brand-dot"></span>
      <span class="brand-name">Crossing the Stream</span>
    </div>
    <ul class="contact">
      <li class="contact-item">
        <svg class="contact-icon" viewBox="0 0 16 16" aria-hidden="true"><path d="M4 1.5 L6.5 4.5 L5 6 C5.8 8 8 10.2 10 11 L11.5 9.5 L14.5 12 L12.5 14.5 C7 14 2 9 1.5 3.5 Z" fill="none" stroke="var(--ink)" stroke-width="1.3" stroke-linejoin="round"/></svg>
        0508 PCS MENTOR
      </li>
      <li class="contact-item">
        <svg class="contact-icon" viewBox="0 0 16 16" aria-hidden="true"><path d="M4 1.5 L6.5 4.5 L5 6 C5.8 8 8 10.2 10 11 L11.5 9.5 L14.5 12 L12.5 14.5 C7 14 2 9 1.5 3.5 Z" fill="none" stroke="var(--ink)" stroke-width="1.3" stroke-linejoin="round"/></svg>
        021 839 415
      </li>
      <li class="contact-item">
        <svg class="contact-icon" viewBox="0 0 16 16" aria-hidden="true"><path d="M1.5 6 L8 2 L14.5 6 V13.5 H1.5 Z" fill="var(--ink)"/><path d="M2 6.5 L8 10.5 L14 6.5" fill="none" stroke="var(--paper)" stroke-width="1.2"/></svg>
        training@crossingthestream.co.nz
      </li>
    </ul>
  </header>

  <footer>
    <p class="tagline">Computer Training for Educators</p>
    <svg class="footer-bands" viewBox="0 0 1034 46" aria-hidden="true">
      <polygon points="0,25 512,25 480,46 0,46" fill="var(--brand-green)"/>
      <polygon points="557,0 1034,0 1034,46 493,46" fill="var(--brand-blue)"/>
    </svg>
    <p class="web-address">www.crossingthestream.co.nz</p>
  </footer>
</div>
</body>
</html>
```